KDWB Business Card

Looking for a business card design to incorporate our branding. We want to only use the colors listing in the Branding Package (attached).
Updates

Target Market(s)

People who need their phone or device fixed.

Industry/Entity Type

Electronics

Contact Information for Business Card

Please use:

Brightwick Gadget Clinic LLC
4810 E Harlow Ridge Rd
Suite 417
San Antonio, TX 78163

Marcus Delgrove, Store Manager

(210) 555-0147

Requirements
Must have
• Must include the colors that are contained within the Branding Package PDF file.

```html
<!DOCTYPE html>
<html lang="en">
<head>
<meta charset="utf-8">
<title>Brightwick Gadget Clinic – Business Card</title>
<link rel="stylesheet" href="https://fonts.googleapis.com/css2?family=Arimo:wght@400;700&display=swap">
<style>
  :root {
    --brand-orange: #f26a22;
    --brand-orange-deep: #e9541f;
    --card-black: #1e1e1e;
    --card-white: #ffffff;
    --text-light: #f4f4f4;
    --backdrop: #e6e3df;
  }
  * { box-sizing: border-box; margin: 0; padding: 0; }
  html, body { width: 1200px; height: 858px; overflow: hidden; }
  body {
    background: var(--backdrop);
    font-family: "Arimo", Arial, sans-serif;
    position: relative;
  }
  .card {
    position: absolute;
    top: 132px;
    width: 340px;
    height: 594px;
    background: var(--card-white);
    box-shadow: 0 10px 28px rgba(0,0,0,0.18);
    overflow: hidden;
  }
  .card--front { left: 220px; }
  .card--back { left: 640px; }

  .brand {
    display: flex;
    align-items: center;
    gap: 10px;
  }
  .brand__square {
    width: 30px;
    height: 30px;
    background: var(--brand-orange);
    flex: none;
  }
  .brand__name {
    color: var(--brand-orange);
    font-size: 20px;
    font-weight: 400;
    white-space: nowrap;
  }

  .front__header {
    height: 118px;
    display: flex;
    align-items: center;
    justify-content: center;
  }
  .front__body {
    height: 392px;
    background: var(--card-black);
    padding: 46px 24px 0;
    text-align: center;
  }
  .person__name {
    color: var(--text-light);
    font-size: 33px;
    font-weight: 400;
    letter-spacing: 0.5px;
  }
  .person__title {
    color: var(--brand-orange);
    font-size: 19px;
    margin-top: 4px;
  }
  .contact__phone {
    color: var(--brand-orange);
    font-size: 31px;
    letter-spacing: 1.5px;
    margin-top: 42px;
  }
  .contact__address {
    color: var(--text-light);
    font-size: 15px;
    line-height: 1.45;
    letter-spacing: 0.6px;
    margin-top: 40px;
    font-style: normal;
  }
  .front__footer {
    height: 84px;
    background: linear-gradient(90deg, var(--brand-orange-deep), var(--brand-orange));
    display: flex;
    align-items: center;
    justify-content: center;
  }
  .contact__web {
    color: var(--card-white);
    font-size: 17px;
    letter-spacing: 0.4px;
  }

  .back__brand {
    position: absolute;
    left: 70px;
    bottom: 150px;
    transform-origin: left bottom;
    transform: rotate(90deg) translate(-150px, 0);
  }
</style>
</head>
<body>
  <section class="card card--front" aria-label="Business card front">
    <header class="front__header">
      <div class="brand">
        <span class="brand__square"></span>
        <span class="brand__name">Brightwick Gadget Clinic</span>
      </div>
    </header>
    <div class="front__body">
      <h1 class="person__name">Marcus Delgrove</h1>
      <p class="person__title">Store Manager</p>
      <p class="contact__phone">(210) 555-0147</p>
      <address class="contact__address">
        4810 E Harlow Ridge Rd<br>
        Suite 417<br>
        San Antonio, TX 78163
      </address>
    </div>
    <footer class="front__footer">
      <span class="contact__web">www.BrightwickGadgetClinic.com</span>
    </footer>
  </section>

  <section class="card card--back" aria-label="Business card back">
    <div class="brand back__brand">
      <span class="brand__square"></span>
      <span class="brand__name">Brightwick Gadget Clinic</span>
    </div>
  </section>
</body>
</html>
```